Law Firm Business Card

This is a business card for a law firm that serves US military and veterans.

The card must have ONLY the following (we want an uncluttered look):

- Company logo (PNG, GIF, JPEG copies uploaded)
- A tagline reading: "a law firm for service members and veterans"
- My name and title: "Tobias Marlow" and "Attorney"
- My email: "tobias.marlow@brinmoorlegal.com"
- My number: "855-FIRM-ONE (347-6663)"

We are looking for a clean, simple layout with only the above information, likely printed on a bright white cotton stock. The font of our logo is DIN 1451, and the font used on our website is Helvetica Neue. The color of our logo is #336699, and we probably want the tagline in that color also, and my contact information in a dark grey. Please review our website at www.brinmoorlegal.com to ensure your card design complements our website style.

Thanks and we look forward to seeing your submissions.

A few notes:

- Two-sided submissions are ok
- Please don't add graphics (scales of justice, judges hammer, etc)

```html
<!DOCTYPE html>
<html lang="en">
<head>
<meta charset="utf-8">
<title>Brinmoor Legal – Business Card</title>
<link rel="stylesheet" href="https://fonts.googleapis.com/css2?family=Barlow+Condensed:wght@600&family=Barlow:wght@500&family=Tinos&display=swap">
<style>
  :root {
    --brand-blue: #2767cc;
    --ink: #1e1e1e;
    --card-white: #f7f7f7;
    --backdrop: #e4e4e4;
    --divider: #c9c9c9;
  }
  * { margin: 0; padding: 0; box-sizing: border-box; }
  html, body { width: 1200px; height: 1049px; overflow: hidden; }
  body { background: var(--backdrop); position: relative; }

  .card {
    position: absolute;
    width: 680px;
    height: 388px;
    box-shadow: 0 6px 18px rgba(0,0,0,.18);
  }

  /* Front */
  .card-front {
    left: 60px; top: 70px;
    background: linear-gradient(135deg, #fff 0%, var(--card-white) 100%);
  }
  .edge-band {
    position: absolute; left: 0; top: 0; width: 16px; height: 100%;
  }
  .front-wordmark {
    position: absolute; left: 44px; top: 40px;
    font-family: "Barlow Condensed", sans-serif;
    font-weight: 600; font-size: 62px; line-height: 1;
    color: var(--brand-blue); letter-spacing: 1px; text-transform: uppercase;
  }
  .details {
    position: absolute; left: 372px; top: 150px;
    padding-left: 22px; border-left: 2px solid var(--divider);
    height: 196px;
  }
  .name-line {
    font-family: "Barlow", sans-serif; font-weight: 500; font-size: 25px;
    color: var(--brand-blue);
  }
  .name-line .title { color: var(--ink); font-size: 18px; }
  .tagline {
    font-family: "Tinos", serif; font-size: 21px; line-height: 1.15;
    color: var(--brand-blue); margin-top: 4px;
  }
  .contact-list { list-style: none; margin-top: 18px; }
  .contact-list li {
    display: flex; align-items: center; gap: 10px;
    font-family: "Barlow", sans-serif; font-weight: 500; font-size: 16px;
    color: var(--ink); margin-bottom: 8px; white-space: nowrap;
  }
  .contact-list svg { width: 18px; height: 18px; flex: none; }

  /* Back */
  .card-back {
    left: 470px; top: 600px;
    background: var(--brand-blue);
    display: flex; align-items: center; justify-content: center;
  }
  .back-wordmark {
    font-family: "Barlow Condensed", sans-serif;
    font-weight: 600; font-size: 96px; line-height: 1;
    color: #fff; letter-spacing: 2px; text-transform: uppercase;
  }
</style>
</head>
<body>

<section class="card card-front">
  <svg class="edge-band" viewBox="0 0 16 388" preserveAspectRatio="none" aria-hidden="true">
    <path d="M0 0 H8 V170 Q16 180 8 190 V388 H0 Z" fill="var(--brand-blue)"/>
  </svg>
  <div class="front-wordmark">Brinmoor Legal</div>

  <div class="details">
    <p class="name-line">Tobias Marlow<span class="title">, Attorney</span></p>
    <p class="tagline">A Law Firm For Service Members<br>And Veterans</p>
    <ul class="contact-list">
      <li>
        <svg viewBox="0 0 20 20" aria-hidden="true"><circle cx="10" cy="10" r="8.5" fill="none" stroke="var(--brand-blue)" stroke-width="1.5"/><path d="M7 5.5 L9 7.5 L8 9 Q9 11.5 11 12 L12.5 11 L14.5 13 L13 14.5 Q8 14 5.5 7 Z" fill="var(--brand-blue)"/></svg>
        855-FIRM-ONE (347-6663)
      </li>
      <li>
        <svg viewBox="0 0 20 20" aria-hidden="true"><rect x="2" y="5" width="16" height="11" rx="1.5" fill="var(--brand-blue)"/><path d="M2.5 6 L10 11.5 L17.5 6" fill="none" stroke="#fff" stroke-width="1.4"/></svg>
        tobias.marlow@brinmoorlegal.com
      </li>
      <li>
        <svg viewBox="0 0 20 20" aria-hidden="true"><g fill="none" stroke="var(--brand-blue)" stroke-width="1.4"><circle cx="10" cy="10" r="7.5"/><ellipse cx="10" cy="10" rx="3.2" ry="7.5"/><path d="M2.5 10 H17.5 M4 6 H16 M4 14 H16"/></g></svg>
        www.brinmoorlegal.com
      </li>
    </ul>
  </div>
</section>

<section class="card card-back">
  <div class="back-wordmark">Brinmoor Legal</div>
</section>

</body>
</html>
```